VOMRA Pty Ltd Business Card

Looking for a simple yet eye-catching double-sided business card design using my company logo on one side and contact details on the other.

Target Market(s)

Government

Industry/Entity Type

Communication Systems Engineering

Contact Information for Business Card

VOMRA Pty Ltd

Requirements
Nice to have
• Would be great to have a QR code so details can be scanned into contacts

```html
<!DOCTYPE html>
<html lang="en">
<head>
<meta charset="utf-8">
<title>VOMRA Pty Ltd Business Card</title>
<link href="https://fonts.googleapis.com/css2?family=Open+Sans:wght@400;600;700&display=swap" rel="stylesheet">
<style>
  :root {
    --backdrop: #232323;
    --slate: #37414a;
    --paper: #ffffff;
    --ink: #37414a;
    --text: #1f2328;
  }
  * { margin: 0; padding: 0; box-sizing: border-box; }
  html, body { width: 1200px; height: 780px; overflow: hidden; background: var(--backdrop); }
  body { font-family: "Open Sans", sans-serif; position: relative; }

  .card {
    position: absolute;
    top: 75px;
    width: 360px;
    height: 630px;
    border-radius: 26px;
    overflow: hidden;
  }
  .card--back { left: 210px; background: var(--slate); }
  .card--front { left: 630px; background: var(--paper); color: var(--text); }

  /* Back side */
  .back-wordmark {
    position: absolute;
    left: 50%;
    top: 215px;
    transform: translate(-50%, -50%) rotate(90deg);
    color: var(--paper);
    font-weight: 700;
    font-size: 92px;
    letter-spacing: 6px;
    white-space: nowrap;
  }
  .back-mark {
    position: absolute;
    left: 50%;
    top: 445px;
    width: 120px;
    height: 120px;
    margin-left: -60px;
    border-radius: 50%;
    background: var(--paper);
  }

  /* Front side */
  .front-logo {
    position: absolute;
    top: 60px;
    left: 0; right: 0;
    display: flex;
    align-items: center;
    justify-content: center;
    gap: 18px;
  }
  .front-logo__dot { width: 70px; height: 70px; border-radius: 50%; background: var(--ink); }
  .front-logo__name { font-weight: 700; font-size: 56px; letter-spacing: 3px; color: var(--ink); }

  .identity { position: absolute; top: 335px; left: 0; right: 0; text-align: center; }
  .identity__name { font-weight: 700; font-size: 34px; color: var(--ink); line-height: 1.1; }
  .identity__role { font-weight: 600; font-size: 14px; color: var(--text); }

  .divider { position: absolute; left: 20px; width: 320px; height: 26px; }
  .divider--top { top: 397px; }
  .divider--bottom { top: 508px; }

  .contact-lines {
    position: absolute; top: 428px; left: 0; right: 0;
    text-align: center; font-size: 17px; line-height: 24px;
  }
  .address {
    position: absolute; top: 540px; left: 0; right: 0;
    text-align: center; font-size: 17px; line-height: 24px;
  }
</style>
</head>
<body>

<section class="card card--back" aria-label="Card back">
  <div class="back-wordmark">VOMRA</div>
  <div class="back-mark"></div>
</section>

<section class="card card--front" aria-label="Card front">
  <div class="front-logo">
    <span class="front-logo__dot"></span>
    <span class="front-logo__name">VOMRA</span>
  </div>

  <div class="identity">
    <p class="identity__name">Jordan Hale</p>
    <p class="identity__role">Co-Founder</p>
  </div>

  <svg class="divider divider--top" viewBox="0 0 320 26" aria-hidden="true">
    <g fill="#37414a">
      <circle cx="6" cy="13" r="2.5"/><circle cx="20" cy="13" r="3.5"/><circle cx="36" cy="13" r="4.5"/>
      <circle cx="54" cy="13" r="5.5"/><circle cx="74" cy="13" r="6.5"/><circle cx="96" cy="13" r="7.5"/>
      <circle cx="130" cy="13" r="12"/><circle cx="160" cy="13" r="12"/><circle cx="190" cy="13" r="12"/>
      <circle cx="224" cy="13" r="7.5"/><circle cx="246" cy="13" r="6.5"/><circle cx="266" cy="13" r="5.5"/>
      <circle cx="284" cy="13" r="4.5"/><circle cx="300" cy="13" r="3.5"/><circle cx="314" cy="13" r="2.5"/>
    </g>
    <!-- phone -->
    <path d="M125 7c1-1 2-1 3 0l2 2c1 1 0 2-1 2.5 .5 1.5 2 3 3.5 3.5 .5-1 1.5-2 2.5-1l2 2c1 1 1 2 0 3-3 2-9-2-11-7-1-2-1.5-3.5-1-5z" fill="#fff"/>
    <!-- email -->
    <rect x="153" y="8" width="14" height="10" fill="none" stroke="#fff" stroke-width="1.5"/>
    <path d="M153 8l7 6 7-6" fill="none" stroke="#fff" stroke-width="1.5"/>
    <!-- globe -->
    <circle cx="190" cy="13" r="7" fill="none" stroke="#fff" stroke-width="1.5"/>
    <ellipse cx="190" cy="13" rx="3" ry="7" fill="none" stroke="#fff" stroke-width="1.2"/>
    <line x1="183" y1="13" x2="197" y2="13" stroke="#fff" stroke-width="1.2"/>
  </svg>

  <div class="contact-lines">
    <p>(555) 410-2286</p>
    <p>www.vomra.com.au</p>
    <p>admin@vomra.com.au</p>
  </div>

  <svg class="divider divider--bottom" viewBox="0 0 320 26" aria-hidden="true">
    <g fill="#37414a">
      <circle cx="6" cy="13" r="2.5"/><circle cx="20" cy="13" r="3.5"/><circle cx="36" cy="13" r="4.5"/>
      <circle cx="54" cy="13" r="5.5"/><circle cx="74" cy="13" r="6.5"/><circle cx="96" cy="13" r="7.5"/>
      <circle cx="120" cy="13" r="8.5"/><circle cx="160" cy="13" r="12"/>
      <circle cx="200" cy="13" r="8.5"/><circle cx="224" cy="13" r="7.5"/><circle cx="246" cy="13" r="6.5"/>
      <circle cx="266" cy="13" r="5.5"/><circle cx="284" cy="13" r="4.5"/><circle cx="300" cy="13" r="3.5"/>
      <circle cx="314" cy="13" r="2.5"/>
    </g>
    <!-- pin -->
    <path d="M160 21c-3-4-6-7-6-10a6 6 0 0 1 12 0c0 3-3 6-6 10z" fill="#fff"/>
    <circle cx="160" cy="11" r="2.2" fill="#37414a"/>
  </svg>

  <div class="address">
    <p>42-44 Harbour Lane Eastwood</p>
    <p>NSW 2122 Australia</p>
  </div>
</section>

</body>
</html>
```